MRT Property - Business Cards

Looking for a business card & general letterhead, signage etc design for our new logo.

Colours:
000a20
0056a2
00b5ef
0088ce
68cef2

Fonts:
Poppins
Karla

Please keep look and feel of new brand - example in the zip package I sent.

```html
<!DOCTYPE html>
<html lang="en">
<head>
<meta charset="utf-8">
<title>MRT Property – Business Cards</title>
<link href="https://fonts.googleapis.com/css2?family=Montserrat:wght@400;500;700&family=Neucha&display=swap" rel="stylesheet">
<style>
  :root {
    --ink: #000a20;
    --brand-blue: #0b56a5;
    --mid-blue: #0088ce;
    --sky-blue: #00b5ef;
    --pale-blue: #68cef2;
    --paper: #ffffff;
    --backdrop: #999999;
    --text-dark: #222222;
  }
  * { margin: 0; padding: 0; box-sizing: border-box; }
  html, body {
    width: 1093px;
    height: 1200px;
    overflow: hidden;
    background: var(--backdrop);
    font-family: "Montserrat", sans-serif;
  }
  .card {
    position: absolute;
    left: 264px;
    width: 581px;
    height: 363px;
    border-radius: 21px;
    overflow: hidden;
  }
  .card--front { top: 225px; background: var(--paper); }
  .card--back  { top: 616px; height: 366px; background: var(--brand-blue); }

  .wordmark {
    position: absolute;
    font-family: "Montserrat", sans-serif;
    font-weight: 700;
    white-space: nowrap;
  }
  .card--front .wordmark {
    left: 23px;
    top: 48px;
    font-size: 36px;
    color: var(--brand-blue);
    letter-spacing: 0.5px;
  }
  .card--back .wordmark {
    left: 0;
    right: 0;
    top: 150px;
    text-align: center;
    font-size: 52px;
    color: var(--paper);
  }

  .holder {
    position: absolute;
    right: 34px;
    top: 26px;
    text-align: right;
  }
  .holder__name {
    font-family: "Neucha", cursive;
    font-size: 27px;
    line-height: 1;
    color: var(--brand-blue);
  }
  .holder__title {
    font-size: 12.5px;
    font-weight: 500;
    color: var(--text-dark);
    margin-top: 3px;
  }
  .holder-tab {
    position: absolute;
    right: 0;
    top: 26px;
    width: 20px;
    height: 46px;
    background: var(--brand-blue);
  }

  .address {
    position: absolute;
    left: 24px;
    top: 200px;
    font-size: 13.5px;
    line-height: 17px;
    color: var(--text-dark);
  }
  .contacts {
    position: absolute;
    left: 26px;
    top: 265px;
    list-style: none;
  }
  .contacts li {
    display: flex;
    align-items: center;
    height: 24.5px;
    font-size: 13px;
    color: var(--text-dark);
  }
  .contacts svg {
    width: 13px;
    height: 13px;
    margin-right: 9px;
    fill: var(--mid-blue);
    flex: none;
  }
  .base-band {
    position: absolute;
    left: 0;
    right: 0;
    bottom: 0;
    height: 21px;
    background: var(--brand-blue);
  }
</style>
</head>
<body>

<section class="card card--front" aria-label="Business card front">
  <div class="wordmark">MRT Property</div>

  <div class="holder">
    <div class="holder__name">Daniel Harper</div>
    <div class="holder__title">Managing Director</div>
  </div>
  <div class="holder-tab"></div>

  <p class="address">42 Cedar Hollow Lane<br>Ridgeford, MS 39040</p>

  <ul class="contacts">
    <li>
      <svg viewBox="0 0 24 24" aria-hidden="true"><path d="M6.6 10.8a15.1 15.1 0 0 0 6.6 6.6l2.2-2.2a1 1 0 0 1 1-.25 11.4 11.4 0 0 0 3.6.57 1 1 0 0 1 1 1V20a1 1 0 0 1-1 1A17 17 0 0 1 3 4a1 1 0 0 1 1-1h3.5a1 1 0 0 1 1 1c0 1.25.2 2.45.57 3.57a1 1 0 0 1-.25 1z"/></svg>
      555.014.2276
    </li>
    <li>
      <svg viewBox="0 0 24 24" aria-hidden="true"><path d="M2 5h20v14H2z M2 6l10 7 10-7" /></svg>
      info@mrtproperty.com
    </li>
    <li>
      <svg viewBox="0 0 24 24" aria-hidden="true"><circle cx="12" cy="12" r="10"/></svg>
      www.mrtproperty.com
    </li>
  </ul>

  <div class="base-band"></div>
</section>

<section class="card card--back" aria-label="Business card back">
  <div class="wordmark">MRT Property</div>
</section>

</body>
</html>
```